Web design

We need the design for the logo and website for a women fashion website. No coding required. The colors used should be neutral (maybe with a light touch of color), the style should be modern, slightly luxurious, not too crowded. The target market is young professionals who love trendy clothes.
Updates

Need extra days to review

Target Market(s)

Young professionals

Industry/Entity Type

Apparel

Number of Pages Required

5+ page

Font styles to use
Sans Serif
Other font styles liked:
• Montserrat, Engravers Gothic, Benton Sans, gotham-book

Colors

Designer to choose colors to be used in the design.

```html
<!DOCTYPE html>
<html lang="en">
<head>
<meta charset="utf-8">
<title>VERA – Checkout</title>
<link href="https://fonts.googleapis.com/css2?family=Roboto:wght@400;500;700&family=Montserrat:wght@400;500;600&family=Hind:wght@400;500&display=swap" rel="stylesheet">
<style>
:root{
  --ink:#1f1f1f;
  --navy:#26223a;
  --gold:#d9a514;
  --gold-soft:#ecc865;
  --sale:#ee3a2c;
  --muted:#b8b8b8;
  --step-off:#e2e2e2;
  --line:#e6e6e6;
  --table-head:#f4f4f4;
  --footer:#f4f3f1;
  --white:#ffffff;
}
*{margin:0;padding:0;box-sizing:border-box}
html,body{width:1190px;height:1200px;overflow:hidden;background:var(--white);color:var(--ink);font-family:'Roboto',sans-serif}
.header{position:absolute;left:0;top:0;width:1190px;height:75px;border-bottom:1px solid var(--line)}
.nav a{position:absolute;top:30px;font-size:15px;color:var(--ink);text-decoration:none;white-space:nowrap}
.nav .sale{color:var(--sale)}
.brand-name{position:absolute;left:552px;top:36px;width:120px;text-align:center;font-family:'Montserrat',sans-serif;font-weight:500;font-size:28px;line-height:30px;letter-spacing:1px;color:var(--navy)}
.tools svg{position:absolute}
.lang{position:absolute;left:956px;top:33px;font-size:11px;display:flex;align-items:center;gap:4px}
.badge{position:absolute;left:1078px;top:29px;width:13px;height:13px;border-radius:50%;background:var(--gold);color:#fff;font-size:8px;text-align:center;line-height:13px}
.page-title{position:absolute;left:0;width:1190px;top:124px;text-align:center;font-size:41px;font-weight:700;letter-spacing:.5px}
.step{position:absolute;top:200px;height:40px;display:flex;align-items:center;gap:16px;font-size:14.5px;color:var(--muted);white-space:nowrap;font-weight:500}
.step .num{width:40px;height:40px;border-radius:50%;background:var(--step-off);color:#fff;font-size:22px;display:flex;align-items:center;justify-content:center}
.step.active{color:var(--ink)}
.step.active .num{background:var(--gold)}
.section-title{position:absolute;left:197px;top:305px;font-family:'Montserrat',sans-serif;font-weight:600;font-size:31px;letter-spacing:.3px}
.rule{position:absolute;left:199px;top:351px;width:791px;height:1px;background:#cfcfcf}
.rule::before{content:"";position:absolute;left:0;top:0;width:280px;height:1px;background:var(--gold-soft)}
.cart{position:absolute;left:199px;top:389px;width:792px;border-collapse:collapse;font-family:'Hind',sans-serif;border:1px solid #eee}
.cart th{height:46px;background:var(--table-head);font-family:'Roboto',sans-serif;font-weight:400;font-size:13.5px;letter-spacing:.2px}
.cart td{border:1px solid #eee;text-align:center;font-size:16.5px}
.cart tr.item td{height:74px}
.col-name{width:281px}.col-qty{width:179px}.col-price{width:169px}
.product{display:flex;align-items:center;gap:12px;padding-left:8px;text-align:left}
.thumb{width:46px;height:58px;background:linear-gradient(160deg,#cfc6bc,#a89a8c 60%,#e4ddd5)}
.product h3{font-weight:500;font-size:16.5px;line-height:18px}
.product p{font-size:12.5px;color:#555;margin-top:5px}
.qty{display:inline-flex;border:1px solid #cfcfcf;height:31px;font-family:'Roboto',sans-serif}
.qty span{width:30px;display:flex;align-items:center;justify-content:center;font-size:12px}
.qty span+span{border-left:1px solid #cfcfcf}
.sub{display:inline-flex;align-items:center;gap:8px;margin-left:40px}
.remove{width:19px;height:19px}
.cart tr.total td{height:45px;background:var(--table-head);text-align:right;padding-right:30px;border:none}
.total small{font-family:'Roboto',sans-serif;font-size:9px;letter-spacing:.3px}
.total strong{font-family:'Roboto',sans-serif;font-size:17px;font-weight:500}
.order-btn{position:absolute;left:476px;top:738px;width:238px;height:50px;background:var(--ink);color:#fff;font-weight:500;font-size:17px;display:flex;align-items:center;justify-content:center}
.footer{position:absolute;left:0;top:871px;width:1190px;height:329px;background:var(--footer);font-family:'Montserrat',sans-serif}
.footer .bigname{position:absolute;left:86px;top:146px;font-family:'Montserrat',sans-serif;font-weight:500;font-size:52px;line-height:60px;color:var(--navy);letter-spacing:2px}
.fcol{position:absolute;top:79px}
.fcol h4{font-weight:600;font-size:15px;letter-spacing:.8px;margin-bottom:17px}
.fcol li{list-style:none;font-size:13.5px;height:26.3px;color:#333;display:flex;align-items:center;gap:14px}
.fcol .dot{width:10px;height:10px;border-radius:50%;background:var(--ink);display:inline-block}
.footer .hr{position:absolute;left:111px;top:269px;width:968px;height:1px;background:#cfcfcf}
.legal{position:absolute;left:0;width:1190px;top:287px;text-align:center;font-size:13.5px;color:#333}
</style>
</head>
<body>
<header class="header">
  <nav class="nav">
    <a style="left:102px">Latest Arrivals</a>
    <a style="left:220px">Clothes <svg width="9" height="6" viewBox="0 0 9 6"><path d="M1 1l3.5 3.5L8 1" fill="none" stroke="#1f1f1f" stroke-width="1.2"/></svg></a>
    <a style="left:311px">VERA Club</a>
    <a class="sale" style="left:412px">On Sale</a>
  </nav>
  <div class="brand-name">VERA</div>
  <div class="tools">
    <svg style="left:912px;top:32px" width="16" height="16" viewBox="0 0 16 16"><circle cx="7" cy="7" r="5.5" fill="none" stroke="#1f1f1f" stroke-width="1.4"/><path d="M11 11l4 4" stroke="#1f1f1f" stroke-width="1.4"/></svg>
    <span class="lang">ENG <svg width="7" height="5" viewBox="0 0 7 5"><path d="M1 1l2.5 2.5L6 1" fill="none" stroke="#1f1f1f"/></svg></span>
    <svg style="left:1001px;top:31px" width="23" height="21" viewBox="0 0 23 21"><path d="M11.5 19S1.5 12.5 1.5 6.5A4.8 4.8 0 0 1 11.5 4a4.8 4.8 0 0 1 10 2.5c0 6-10 12.5-10 12.5z" fill="none" stroke="#1f1f1f" stroke-width="1.5"/></svg>
    <svg style="left:1034px;top:28px" width="22" height="24" viewBox="0 0 22 24"><circle cx="11" cy="7" r="5" fill="none" stroke="#1f1f1f" stroke-width="1.5"/><path d="M1.5 23a9.5 9.5 0 0 1 19 0" fill="none" stroke="#1f1f1f" stroke-width="1.5"/></svg>
    <svg style="left:1065px;top:31px" width="20" height="22" viewBox="0 0 20 22"><rect x="1.5" y="7" width="17" height="14" fill="none" stroke="#1f1f1f" stroke-width="1.5"/><path d="M6 7V5a4 4 0 0 1 8 0v2" fill="none" stroke="#1f1f1f" stroke-width="1.5"/></svg>
    <span class="badge">0</span>
  </div>
</header>

<h1 class="page-title">CHECKOUT</h1>

<div class="step" style="left:185px"><span class="num">1</span>BILLING DETAILS</div>
<div class="step" style="left:397px"><span class="num">2</span>SHIPPING DETAILS</div>
<div class="step active" style="left:621px"><span class="num">3</span>REVIEW &amp; PAYMENT</div>
<div class="step" style="left:853px"><span class="num">4</span>CONIRMATION</div>

<h2 class="section-title">REVIEW &amp; PAYMENT</h2>
<div class="rule"></div>

<table class="cart">
  <thead><tr><th class="col-name">PRODUCT NAME</th><th class="col-qty">QUANTITY</th><th class="col-price">UNIT PRICE</th><th>SUBTOTAL</th></tr></thead>
  <tbody>
    <tr class="item">
      <td><div class="product"><div class="thumb" role="img" aria-label="Product photo of a model wearing a white lace top"></div><div><h3>The standard Lorem</h3><p>Lorem ipsum dolor sit amet</p></div></div></td>
      <td><div class="qty"><span>—</span><span>1</span><span style="font-size:17px">+</span></div></td>
      <td>$221.99</td>
      <td><div class="sub">$221.99 <svg class="remove" viewBox="0 0 20 20"><circle cx="10" cy="10" r="9" fill="none" stroke="#555"/><path d="M7 7l6 6M13 7l-6 6" stroke="#555"/></svg></div></td>
    </tr>
    <tr class="item">
      <td><div class="product"><div class="thumb" style="width:38px;margin:0 4px" role="img" aria-label="Product photo of a model wearing a beige knit dress"></div><div><h3>The standard Lorem Ipsum</h3><p>Lorem ipsum dolor sit amet</p></div></div></td>
      <td><div class="qty"><span>—</span><span>1</span><span style="font-size:17px">+</span></div></td>
      <td>$221.99</td>
      <td><div class="sub">$221.99 <svg class="remove" viewBox="0 0 20 20"><circle cx="10" cy="10" r="9" fill="none" stroke="#555"/><path d="M7 7l6 6M13 7l-6 6" stroke="#555"/></svg></div></td>
    </tr>
    <tr class="item">
      <td><div class="product"><div class="thumb" role="img" aria-label="Product photo of a model wearing a white lace top"></div><div><h3>The standarpsum passag</h3><p>Lorem ipsum dolor sit amet</p></div></div></td>
      <td><div class="qty"><span>—</span><span>1</span><span style="font-size:17px">+</span></div></td>
      <td>$221.99</td>
      <td><div class="sub">$221.99 <svg class="remove" viewBox="0 0 20 20"><circle cx="10" cy="10" r="9" fill="none" stroke="#555"/><path d="M7 7l6 6M13 7l-6 6" stroke="#555"/></svg></div></td>
    </tr>
    <tr class="total"><td colspan="4"><small>TOTAL:</small> <strong>$572.97</strong></td></tr>
  </tbody>
</table>

<div class="order-btn">PLACE YOUR ORDER &gt;&gt;</div>

<footer class="footer">
  <div class="bigname">VERA</div>
  <div class="fcol" style="left:398px"><h4>HELP</h4><ul><li>Email Address</li><li>Returns/exchanges</li><li>Delivery Information</li><li>FAQ</li></ul></div>
  <div class="fcol" style="left:656px"><h4>SHOP</h4><ul><li>Tops</li><li>Bootoms</li><li>Intimates</li><li>Dresses</li><li>Swim</li></ul></div>
  <div class="fcol" style="left:938px"><h4>FOLLOW US</h4><ul><li><span class="dot"></span>Friendly</li><li><span class="dot"></span>Chirper</li><li><span class="dot"></span>Snapgram</li><li><span class="dot"></span>Worklink</li></ul></div>
  <div class="hr"></div>
  <p class="legal">Terms &amp; Conditions, Privacy Policy and @2021 followed by vera.</p>
</footer>
</body>
</html>
```